Podiatry (services) Business Card

I need a business design for a New Podiatry Service.
the Podiatry services will include all aspects of podiatry including;
general podiatry for all ages
corns and callus treatment
Ingrown toenails & nail surgery
Forefoot, arch and heel pain
Gait analysis
Sports Podiatry and Orthotics
Paediatric Assessments
Diabetes Foot Assessment

I would like the back of the card to have space for next appointment day and time.

I would like a nice design that is simple yet catchy. I don't like cluttered business cards. I like things to be simple yet stand out because of the finer details.

I like the colours blue and white but I'm open to other designs that have different colours.

Business

Bluewren Podiatry (Business name)

Marisol Tenbury - Podiatrist
M.Pod.P., B.Hlth. Sci, MFLsoc

Address: 58 Coleby St, Marrowdale North Vic, 3164
Phone: (03) 9416 2738
Fax: (03) 9523 4178

```html
<!DOCTYPE html>
<html lang="en">
<head>
<meta charset="utf-8">
<title>Bluewren Podiatry – Business Card</title>
<link href="https://fonts.googleapis.com/css2?family=Open+Sans:wght@400;600&display=swap" rel="stylesheet">
<style>
  :root {
    --brand-blue: #0a7cc6;
    --white: #ffffff;
    --ink: #2b2b2b;
    --backdrop: #eceff2;
  }
  html, body {
    margin: 0;
    width: 1200px;
    height: 900px;
    overflow: hidden;
    background: var(--backdrop);
    font-family: "Open Sans", Arial, sans-serif;
  }
  .canvas { position: relative; width: 1200px; height: 900px; }

  .card {
    position: absolute;
    border-radius: 16px;
    overflow: hidden;
    box-shadow: 0 6px 18px rgba(0,0,0,0.18);
  }
  .card-front { left: 78px; top: 35px; width: 588px; height: 363px; background: var(--white); }
  .card-back  { left: 390px; top: 506px; width: 565px; height: 350px; background: var(--brand-blue); }

  .band { position: absolute; left: 0; right: 0; }
  .card-front .band { top: 28px; height: 100px; background: var(--brand-blue); }
  .card-back .band  { top: 50px; height: 84px; background: var(--white); }

  .brand-disc {
    position: absolute;
    border-radius: 50%;
  }
  .card-front .brand-disc { left: 190px; top: -26px; width: 208px; height: 208px; background: var(--white); }
  .card-back .brand-disc  { left: 197px; top: 9px; width: 170px; height: 170px; background: var(--brand-blue); }

  .business-name {
    position: absolute;
    left: 0; right: 0;
    text-align: center;
    font-weight: 400;
    letter-spacing: 2px;
    text-transform: uppercase;
    margin: 0;
  }
  .card-front .business-name { top: 144px; font-size: 34px; color: var(--brand-blue); }
  .card-back .business-name  { top: 148px; font-size: 31px; color: var(--white); }

  .contact-lines {
    position: absolute;
    left: 100px; top: 262px;
    font-size: 15px; line-height: 25px; color: var(--ink);
  }
  .contact-lines div { display: flex; align-items: center; gap: 6px; }
  .contact-lines svg { width: 12px; height: 12px; fill: var(--brand-blue); }

  .practitioner {
    position: absolute;
    left: 266px; top: 230px;
    color: var(--ink); font-size: 15px; line-height: 23px;
  }
  .practitioner .person-name { color: var(--brand-blue); font-size: 19px; font-weight: 600; }
  .practitioner .role { font-size: 15px; font-weight: 400; color: var(--ink); }
  .practitioner .address { margin-top: 14px; line-height: 25px; }

  .services {
    position: absolute;
    left: 0; right: 0; top: 225px;
    text-align: center;
    color: var(--white);
    font-size: 15px; font-weight: 600; line-height: 23.5px;
    margin: 0; padding: 0; list-style: none;
  }
  .services .sep { margin: 0 8px; font-weight: 400; }
</style>
</head>
<body>
<div class="canvas">

  <section class="card card-front" aria-label="Card front">
    <div class="band"></div>
    <div class="brand-disc" aria-hidden="true"></div>
    <h1 class="business-name">Bluewren Podiatry</h1>

    <div class="contact-lines">
      <div>(03) 9416 2738
        <svg viewBox="0 0 24 24" aria-label="Phone"><path d="M6.6 10.8a15.1 15.1 0 0 0 6.6 6.6l2.2-2.2c.3-.3.7-.4 1-.2 1.1.4 2.3.6 3.6.6.6 0 1 .4 1 1V20c0 .6-.4 1-1 1A17 17 0 0 1 3 4c0-.6.4-1 1-1h3.5c.6 0 1 .4 1 1 0 1.3.2 2.5.6 3.6.1.3 0 .7-.2 1z"/></svg>
      </div>
      <div>(03) 9523 4178
        <svg viewBox="0 0 24 24" aria-label="Fax"><path d="M7 2h8l3 3v5h2a2 2 0 0 1 2 2v9a1 1 0 0 1-1 1H3a1 1 0 0 1-1-1v-9a2 2 0 0 1 2-2h3zm2 2v6h7V6h-2V4zm-1 10v2h2v-2zm4 0v2h2v-2zm4 0v2h2v-2zm-8 4v2h2v-2zm4 0v2h2v-2zm4 0v2h2v-2z"/></svg>
      </div>
    </div>

    <div class="practitioner">
      <div><span class="person-name">Marisol Tenbury</span> <span class="role">- Podiatrist</span></div>
      <div>M.Pod.P., B.Hlth. Sci, MFLsoc</div>
      <div class="address">58 Coleby St, Marrowdale<br>North Vic, 3164</div>
    </div>
  </section>

  <section class="card card-back" aria-label="Card back">
    <div class="band"></div>
    <div class="brand-disc" aria-hidden="true"></div>
    <h2 class="business-name">Bluewren Podiatry</h2>
    <ul class="services">
      <li>General podiatry for all ages<span class="sep">|</span>Corns and callus treatment</li>
      <li>Ingrown toenails &amp; nail surgery<span class="sep">|</span>Forefoot, arch and heel pain</li>
      <li>Gait analysis<span class="sep">|</span>Sports Podiatry and Orthotics</li>
      <li>Paediatric Assessments<span class="sep">|</span>Diabetes Foot Assessment</li>
    </ul>
  </section>

</div>
</body>
</html>
```